Velvet Loom (E-commerce) Website for Embroidery shop

Briefing:

Velvet Loom is an online personalized embroidery shop targeting mainly three customer segments:
1) lovers and marring couples
2) close friends wishing to give unique gifts
3) moms with new born baby personalized gifts

These customers are being served through our three major business lines:
1) Bathrobes and towels with personalized embroidery
2) Embroidered pillows and cushions
3) baby gifts with costumed baby sets stitched

Requirements:

The business has been recently established with moderate variety of products introduced so far. The website must consists of four major pages; a home page and three pages for every single business line. All images necessary for the web design are shareable upon request for copyright reasons if necessary. Please post a few products in each page to make it easy for the employee to use as benchmarks to upload other products.

The website also should contain all items and buttons exist in any e-commerce website such as:

1- social links:
a. (Major) Instagram: https://www.instagram.com/velvet.loom.studio/
b. Twitter: https://twitter.com/Velvet_Loom_
c. Facebook: https://www.facebook.com/Velvet.loom.studio/
d. Snapchat: coming soon

2- Help:
a. Delivery & Returns (inside KSA)
I. Delivery:
- Rush: within 3 business days (SAR 90)
- Express: within 5 business days (SAR 65)
- Standard: 7-10 business days ( SAR 35)
II. Returns: We guarantee you will love our product. But if you don't like it, send it back to us within two days from delivery and we will donate it to a charity and return your money subject to our terms and conditions.

b. Contact:
- Email: Velvet.loom.studio@plumemail.net
- (Mobile) Whats-app: +966 54 312 9067 (for quick response)

d. Warranty:
for only SAR 20 per product, we will give you a lifetime warranty over our German stitches

3- Payment options:
bank transfer, visa, MasterCard and PayPal

Remarks:

- This website is mainly aimed at customers in Saudi Arabia where some contents may not appeal to people from such country and results in your participation being excluded from the contest.

- You are the expert and if I am a webdesigner, I would have not posted this contest, so please use your our own judgment and creativity to come up with the best experience possible.

- Use our Instagram account as your first reference to understand our business as it is our major channel that has been used to reach our customers. Please don't use the pictures with poor quality as we will be replacing them with other images with better quality.

- We intend to have this website bilingual (i.e English and Arabic), so if you can translate it into Arabic, then we will pay you an extra $100 in addition to the contest price.

- If in doubt, please feel free to ask any question and suggestions are always encouraged and warm welcomed.

- If you succeed in this contest, you will be chosen as our ultimate Web designer. That means you will have a long relationship providing services to our customers under one of our businesses that aims at preparing start-up companies establishing their business.

Target Market(s)

1) lovers and marrying couples

Industry/Entity Type

Embroidery

Number of Pages Required

4 page

Font styles to use
Serif
Script

Colors

Designer to choose colors to be used in the design.

Requirements
Must have
• Requirements:
• The business has been recently established with moderate variety of products introduced so far. The website must consists of four major pages; a home page and three pages for every single business line. All images necessary for the web design are shareable upon request for copyright reasons if necessary. Please post a few products in each page to make it easy for the employee to use as benchmarks to upload other products.
• The Website must be also mobile use friendly!!!
• The website also should contain all items and buttons exist in any e-commerce website such as:
• 1- social links:
• a. (Major) Instagram: https://www.instagram.com/velvet.loom.studio/
• b. Twitter: https://twitter.com/Velvet_Loom_
• c. Facebook: https://www.facebook.com/Velvet.loom.studio/
• d. Snapchat: coming soon
• 2- Help:
• a. Delivery & Returns (inside KSA)
• I. Delivery:
• - Rush: within 3 business days (SAR 90)
• - Express: within 5 business days (SAR 65)
• - Standard: 7-10 business days ( SAR 35)
• II. Returns: We guarantee you will love our product. But if you don't like it, send it back to us within two days from delivery and we will donate it to a charity and return your money subject to our terms and conditions.
• b. Contact:
• - Email: Velvet.loom.studio@plumemail.net
• - (Mobile) Whats-app: +966 54 312 9067 (for quick response)
• d. Warranty:
• for only SAR 20 per product, we will give you a lifetime warranty over our German stitches
• 3- Payment options:
• bank transfer, visa, MasterCard and PayPal
• Note: You will be responsible to upload the design to the website fully and ensure its integration and functionality.

```html
<!DOCTYPE html>
<html lang="en">
<head>
<meta charset="utf-8">
<title>Velvet Loom — Personalized Embroidery</title>
<link href="https://fonts.googleapis.com/css2?family=Montserrat:wght@400;600;700&family=Open+Sans:wght@400;600&family=Cinzel:wght@400&display=swap" rel="stylesheet">
<style>
:root{
  --gold:#b08a3e;
  --gold-dark:#8f6e2c;
  --gold-light:#d8c28f;
  --red:#c0392b;
  --pink:#d24d7a;
  --ink:#333;
  --muted:#888;
  --line:#e3e3e3;
  --soft:#f4f4f4;
  --footer:#2a2a2a;
  --footer-bottom:#1e1e1e;
  --white:#fff;
}
*{box-sizing:border-box;margin:0;padding:0}
html,body{width:1200px;height:3472px;overflow:hidden}
body{font-family:"Open Sans",Arial,sans-serif;color:var(--ink);background:var(--white);font-size:13px}
.wrap{width:1080px;margin:0 auto;position:relative}

/* header */
.site-header{height:160px;position:relative}
.brand{position:absolute;left:0;top:22px;display:flex;align-items:center;gap:12px}
.brand-dot{width:44px;height:44px;border-radius:50%;background:var(--gold)}
.brand-name{font-family:"Montserrat",sans-serif;font-weight:700;font-size:28px;color:var(--gold)}
.search{position:absolute;left:370px;top:82px;width:410px;height:36px;border:1px solid var(--line);display:flex;align-items:center;padding:0 14px;color:#aaa}
.search svg{margin-left:auto}
.top-links{position:absolute;right:0;top:28px;font-size:11px;color:#666;display:flex;gap:18px}
.quick-contact{position:absolute;right:0;top:70px;width:230px;font-size:11px;line-height:1.6;color:#555}
.quick-contact h4{color:var(--gold);font-size:11px;font-family:"Montserrat",sans-serif;font-weight:700;letter-spacing:.5px}

.main-nav{height:44px;border-top:1px solid var(--line);border-bottom:1px solid var(--line)}
.main-nav .wrap{display:flex;align-items:center;height:42px;gap:34px;font-family:"Montserrat",sans-serif;font-size:12px;font-weight:600}
.main-nav a{color:var(--ink);text-decoration:none}
.main-nav a.active{color:var(--gold)}
.cart{margin-left:auto;display:flex;align-items:center;gap:8px}

/* hero */
.hero{height:470px;position:relative;background:linear-gradient(100deg,#c9b08a 0%,#e4d6c0 35%,#d9c7ae 55%,#b73a3a 80%,#8f2424 100%)}
.hero-copy{position:absolute;left:0;right:0;top:150px;text-align:center;color:var(--white)}
.hero-copy h1{font-family:"Montserrat",sans-serif;font-weight:700;font-size:54px;text-shadow:0 2px 6px rgba(0,0,0,.35)}
.hero-copy p{font-family:"Montserrat",sans-serif;font-weight:600;font-size:22px;margin-top:6px;text-shadow:0 2px 6px rgba(0,0,0,.35)}
.btn-red{display:inline-block;margin-top:30px;background:var(--red);color:var(--white);font-family:"Montserrat",sans-serif;font-weight:700;font-size:14px;padding:12px 30px}
.arrow-btn{position:absolute;top:205px;width:36px;height:50px;background:rgba(255,255,255,.55);display:flex;align-items:center;justify-content:center}
.arrow-btn.left{left:60px}.arrow-btn.right{right:60px}

/* categories */
.categories{background:var(--soft);height:470px;padding-top:46px}
.cat-grid{display:flex;justify-content:space-between}
.cat-card{width:330px;height:370px;position:relative;border:6px solid var(--white);box-shadow:0 1px 4px rgba(0,0,0,.15)}
.cat-card .cat-img{position:absolute;inset:0}
.cat-card figcaption{position:absolute;left:0;right:0;bottom:16px;text-align:center;color:var(--white);text-shadow:0 1px 4px rgba(0,0,0,.6)}
.cat-card .cat-title{font-family:"Cinzel",serif;font-size:18px}
.cat-card .cat-sub{font-family:"Montserrat",sans-serif;font-weight:700;font-size:14px;margin-top:2px}

/* products */
.products{height:800px;padding-top:40px}
.tabs{display:flex;justify-content:center;gap:90px;font-family:"Cinzel",serif;font-size:26px;color:#666;border-bottom:1px solid var(--line);width:600px;margin:0 auto;padding-bottom:8px}
.tabs .on{color:var(--gold);border-bottom:2px solid var(--gold);margin-bottom:-10px;padding-bottom:8px}
.product-grid{display:grid;grid-template-columns:repeat(4,240px);justify-content:space-between;row-gap:46px;margin-top:46px}
.product .thumb{height:236px;border:1px solid var(--line)}
.product .meta{display:flex;justify-content:space-between;align-items:center;margin-top:10px}
.product .name{font-size:10px;color:var(--pink);font-weight:600;letter-spacing:.4px}
.stars{color:var(--gold);font-size:12px;letter-spacing:1px}
.price{font-family:"Montserrat",sans-serif;font-weight:700;font-size:20px;margin-top:4px}

/* features */
.features{height:400px;background:var(--gold);padding-top:80px}
.feature-grid{display:flex;justify-content:space-between;width:1000px;margin:0 auto}
.feature{width:290px;height:200px;background:var(--white);border:4px solid var(--gold-light);outline:1px solid var(--white);outline-offset:-10px;text-align:center;padding-top:38px}
.feature h3{font-family:"Montserrat",sans-serif;font-weight:700;font-size:17px;margin-top:12px}
.feature p{color:var(--muted);font-size:11px;margin-top:6px}

/* testimonials */
.testimonials{height:460px;padding-top:40px;text-align:center}
.section-title{font-family:"Cinzel",serif;font-size:28px;color:#555}
.quote-box{width:940px;margin:34px auto 0;background:var(--soft);border:1px solid var(--line);padding:26px 60px;position:relative;text-align:left;font-size:12px;line-height:1.7;color:#777;height:150px}
.quote-box .mark{position:absolute;left:24px;top:14px;font-size:40px;color:#bbb;font-family:Georgia,serif}
.quote-box .mark.end{left:auto;right:24px;top:50px}
.more{display:block;text-align:center;margin-top:10px;color:var(--red);font-size:10px;font-weight:600}
.t-arrow{position:absolute;top:68px;color:#aaa;font-size:22px}
.t-arrow.l{left:-40px}.t-arrow.r{right:-40px}
.avatar{width:80px;height:80px;border-radius:50%;margin:26px auto 0;background:radial-gradient(circle,#d7a89a,#a57366)}

/* newsletter */
.newsletter{height:230px;background:#f2efe8;text-align:center;padding-top:40px}
.newsletter .section-title{color:var(--gold)}
.newsletter p{font-size:12px;color:#777;margin-top:6px}
.news-form{display:flex;justify-content:center;margin-top:26px}
.news-form .field{width:500px;height:40px;background:var(--white);border:1px solid var(--line);text-align:left;padding:11px 14px;font-size:12px;color:#999}
.news-form .submit{width:120px;height:40px;background:#222;color:var(--white);font-family:"Cinzel",serif;font-size:14px;line-height:40px;margin-left:14px}

/* footer */
.site-footer{height:392px;background:var(--footer);color:#aaa;padding-top:50px}
.foot-grid{display:flex;justify-content:space-between}
.foot-col h4{font-family:"Montserrat",sans-serif;font-size:12px;font-weight:700;color:var(--white);letter-spacing:.5px;margin-bottom:10px}
.foot-col ul{list-style:none;font-size:12px;line-height:2}
.foot-about{width:240px;font-size:11px;line-height:1.7}
.foot-about .brand-name{font-size:22px;display:block;margin-bottom:14px}
.cards{display:grid;grid-template-columns:repeat(2,52px);gap:8px;margin-bottom:18px}
.cards span{height:32px;background:#ddd;border-radius:3px}
.foot-contact{font-size:11px;line-height:1.8}
.foot-contact h4{color:var(--gold)}
.foot-bottom{height:36px;background:var(--footer-bottom);color:#777;font-size:10px}
.foot-bottom .wrap{display:flex;align-items:center;height:36px}
.socials{margin-left:auto;display:flex;gap:10px}
.socials span{width:14px;height:14px;background:#888;border-radius:2px}
</style>
</head>
<body>

<header class="site-header wrap">
  <div class="brand"><span class="brand-dot"></span><span class="brand-name">Velvet Loom</span></div>
  <div class="search">Search
    <svg width="14" height="14" viewBox="0 0 14 14"><circle cx="6" cy="6" r="4.5" fill="none" stroke="#888" stroke-width="1.5"/><line x1="9.5" y1="9.5" x2="13" y2="13" stroke="#888" stroke-width="1.5"/></svg>
  </div>
  <nav class="top-links"><span>Log In</span><span>My Account</span><span>Wishlist</span><span>Checkout</span><span>Register</span></nav>
  <div class="quick-contact">
    <h4>QUICK CONTACT</h4>
    Velvet.loom.studio@plumemail.net<br>
    Whats-App: +966 54 312 9067
  </div>
</header>

<nav class="main-nav">
  <div class="wrap">
    <a class="active">HOME</a><a>ABOUT</a><a>PRODUCTS</a><a>SHOP</a><a>BLOG</a><a>SPECIALS</a><a>CONTACT US</a>
    <span class="cart">
      <svg width="16" height="14" viewBox="0 0 16 14"><path d="M1 1h3l2 8h8l2-6H5" fill="none" stroke="#333" stroke-width="1.4"/><circle cx="7" cy="12" r="1.3" fill="#333"/><circle cx="13" cy="12" r="1.3" fill="#333"/></svg>
      MY CART 0
    </span>
  </div>
</nav>

<section class="hero" role="img" aria-label="Embroidered towels and a red cushion with personalized names">
  <div class="arrow-btn left"><svg width="12" height="18" viewBox="0 0 12 18"><path d="M10 1L2 9l8 8" fill="none" stroke="#333" stroke-width="2"/></svg></div>
  <div class="arrow-btn right"><svg width="12" height="18" viewBox="0 0 12 18"><path d="M2 1l8 8-8 8" fill="none" stroke="#333" stroke-width="2"/></svg></div>
  <div class="hero-copy">
    <h1>Velvet Loom</h1>
    <p>We are an embroidery shop in Saudi Arabia.</p>
    <span class="btn-red">SHOP NOW</span>
  </div>
</section>

<section class="categories">
  <div class="wrap cat-grid">
    <figure class="cat-card">
      <div class="cat-img" role="img" aria-label="Embroidered bathrobes and towels" style="background:linear-gradient(160deg,#8a7ba0,#c4b6d2 50%,#5a4f6e)"></div>
      <figcaption><div class="cat-title">BATHROBES &amp; TOWELS</div><div class="cat-sub">With Personalized Embroidery</div></figcaption>
    </figure>
    <figure class="cat-card">
      <div class="cat-img" role="img" aria-label="Embroidered pillow with a calendar design" style="background:linear-gradient(160deg,#e9e4e6,#f6f3f4 50%,#bdb3b8)"></div>
      <figcaption><div class="cat-title">EMBROIDERED PILLOWS</div><div class="cat-sub">&amp; Cushions</div></figcaption>
    </figure>
    <figure class="cat-card">
      <div class="cat-img" role="img" aria-label="Baby gift set in a festive outfit" style="background:linear-gradient(160deg,#f1ddd2,#f8efe9 50%,#c98c82)"></div>
      <figcaption><div class="cat-title">BABY GIFTS WITH</div><div class="cat-sub">Costumed Baby Sets Stitched</div></figcaption>
    </figure>
  </div>
</section>

<section class="products wrap">
  <div class="tabs"><span class="on">LATEST</span><span>SPECIAL</span><span>BESTSELLERS</span></div>
  <div class="product-grid">
    <article class="product"><div class="thumb" role="img" aria-label="Grey cushion with embroidered name" style="background:linear-gradient(160deg,#e8e8ea,#c9c9cf)"></div><div class="meta"><span class="name">NAME CUSHION</span><span class="stars">★★★★★</span></div><div class="price">$12.00</div></article>
    <article class="product"><div class="thumb" role="img" aria-label="Purple towel with embroidered name" style="background:linear-gradient(160deg,#b7a2c8,#6f5a86)"></div><div class="meta"><span class="name">NAME TOWEL</span><span class="stars">★★★★★</span></div><div class="price">$12.00</div></article>
    <article class="product"><div class="thumb" role="img" aria-label="Towel set with embroidered names" style="background:linear-gradient(160deg,#cfc3b6,#8c6e5e)"></div><div class="meta"><span class="name">COUPLE SET</span><span class="stars">★★★★★</span></div><div class="price">$12.00</div></article>
    <article class="product"><div class="thumb" role="img" aria-label="Cream pillow with embroidered name" style="background:linear-gradient(160deg,#efe7dc,#c8b79f)"></div><div class="meta"><span class="name">NAME PILLOW</span><span class="stars">★★★★★</span></div><div class="price">$12.00</div></article>
    <article class="product"><div class="thumb" role="img" aria-label="Pink towels with embroidered initials" style="background:linear-gradient(160deg,#f3c4c4,#d9848a)"></div><div class="meta"><span class="name">PINK TOWELS</span><span class="stars">★★★★★</span></div><div class="price">$12.00</div></article>
    <article class="product"><div class="thumb" role="img" aria-label="Embroidered calendar pillow" style="background:linear-gradient(160deg,#f2eeea,#b9aea6)"></div><div class="meta"><span class="name">DATE PILLOW</span><span class="stars">★★★★★</span></div><div class="price">$12.00</div></article>
    <article class="product"><div class="thumb" role="img" aria-label="Navy and purple towels with embroidered names" style="background:linear-gradient(160deg,#5a5f8e,#2d2f55)"></div><div class="meta"><span class="name">NAVY TOWELS</span><span class="stars">★★★★★</span></div><div class="price">$12.00</div></article>
    <article class="product"><div class="thumb" role="img" aria-label="Grey towel with teal embroidered name" style="background:linear-gradient(160deg,#9a9ea3,#5e6469)"></div><div class="meta"><span class="name">GREY TOWEL</span><span class="stars">★★★★★</span></div><div class="price">$12.00</div></article>
  </div>
</section>

<section class="features">
  <div class="feature-grid">
    <div class="feature">
      <svg width="40" height="30" viewBox="0 0 40 30"><rect x="2" y="4" width="22" height="16" fill="#333"/><path d="M24 9h8l6 6v5H24z" fill="#333"/><circle cx="10" cy="23" r="4" fill="#333" stroke="#fff" stroke-width="2"/><circle cx="31" cy="23" r="4" fill="#333" stroke="#fff" stroke-width="2"/></svg>
      <h3>FREE SHIPPING</h3><p>Free shipping all over the country</p>
    </div>
    <div class="feature">
      <svg width="30" height="30" viewBox="0 0 30 30"><rect x="2" y="13" width="6" height="14" fill="#333"/><path d="M10 13l6-10c3 0 4 2 3 5l-1 4h8c2 0 3 2 2 4l-3 9c-1 2-2 2-4 2H10z" fill="#333"/></svg>
      <h3>BEST QUALITY</h3><p>Only the best quality and stitches</p>
    </div>
    <div class="feature">
      <svg width="32" height="30" viewBox="0 0 32 30"><path d="M5 18v-4a11 11 0 0 1 22 0v4" fill="none" stroke="#333" stroke-width="3"/><rect x="2" y="16" width="7" height="10" rx="2" fill="#333"/><rect x="23" y="16" width="7" height="10" rx="2" fill="#333"/></svg>
      <h3>ONLINE SUPPORT</h3><p>Round the clock support 24/7</p>
    </div>
  </div>
</section>

<section class="testimonials">
  <h2 class="section-title">TESTIMONIALS</h2>
  <div class="quote-box">
    <span class="mark">“</span><span class="mark end">”</span>
    <span class="t-arrow l">‹</span><span class="t-arrow r">›</span>
    The towels arrived beautifully wrapped and the stitching of our names was neat, even and elegant. It was the perfect wedding gift for my sister and her husband, and everyone at the party asked where we ordered it. Delivery was quick, the team answered every question on WhatsApp, and the colours matched exactly what we chose. We will surely order the baby set next.
    <a class="more">MORE READING</a>
  </div>
  <div class="avatar" role="img" aria-label="Customer portrait"></div>
</section>

<section class="newsletter">
  <h2 class="section-title">NEWSLETTER SIGN UP</h2>
  <p>Follow a selection of news &amp; promotions</p>
  <div class="news-form"><div class="field">Enter Email Address</div><div class="submit">SIGN UP</div></div>
</section>

<footer class="site-footer">
  <div class="wrap foot-grid">
    <div class="foot-about">
      <span class="brand-name">Velvet Loom</span>
      Personalized embroidery made by hand in Saudi Arabia. Towels, pillows and baby gifts stitched with your names for every special moment.
    </div>
    <div class="foot-col"><h4>NAVIGATION</h4><ul><li>Home</li><li>About</li><li>Product</li><li>Special</li><li>New Arrivals</li><li>Shop</li></ul></div>
    <div class="foot-col"><h4>INFORMATION</h4><ul><li>Blog</li><li>Latest News</li><li>FAQ</li><li>Help</li></ul></div>
    <div class="foot-col"><h4>MY ACCOUNT</h4><ul><li>Log In</li><li>Register</li><li>Wishlist</li><li>My Cart</li></ul></div>
    <div class="foot-col">
      <h4>WE ACCEPT</h4>
      <div class="cards"><span></span><span></span><span></span><span></span></div>
      <div class="foot-contact"><h4>QUICK CONTACT</h4>Velvet.loom.studio@plumemail.net<br>Whats-app: +966 54 312 9067</div>
    </div>
  </div>
</footer>
<div class="foot-bottom">
  <div class="wrap">Copyright © 2024 Velvet Loom. All Rights Reserved
    <div class="socials"><span></span><span></span><span></span><span></span><span></span></div>
  </div>
</div>

</body>
</html>
```